Electrician Business Card/ company logo/small business

New Business Cards and logo needed that will catch peoples eye and say we went that extra step. Attached is a design possibly to be incorporated, if u have your own great, lets see it!... This will be a small local business. thank you for all you do!
Halvern Electric
Ned Fosky Owner
Journeyman Electrician
phone 1.555.208.3471
email: KQLHalvernElectric@quellmail.net
call for free estimate!
Updates

Accepted and approved for cards

Target Market(s)

support small local business

Industry/Entity Type

Electrical,

Contact Information for Business Card

name, title,company/ logo, phone, email, free estimate

Other font styles liked:
• easy to read

Colors

Designer to choose colors to be used in the design.

Requirements
Must have
• eye catching everything! logo and halvern electric listed on business card/logo, incorp logo in the background of card
Nice to have
• lightening bolts in eyes or around the triangle? vertical, modern, any design that would be unique and stand out
Should not have
• pinks, reds, yellows,brown

```html
<!DOCTYPE html>
<html lang="en">
<head>
<meta charset="utf-8">
<title>Halvern Electric – Business Card</title>
<link href="https://fonts.googleapis.com/css2?family=Michroma&family=Arimo:wght@400&display=swap" rel="stylesheet">
<style>
  :root {
    --backdrop: #c4c4c4;
    --card: #1e1e1f;
    --card-back: #262627;
    --blue: #1a8fe3;
    --blue-deep: #0d63c9;
    --white: #f2f2f2;
    --emboss: #5d5d5f;
  }
  * { margin: 0; padding: 0; box-sizing: border-box; }
  html, body { width: 1200px; height: 800px; overflow: hidden; }
  body {
    background: var(--backdrop);
    position: relative;
    font-family: "Arimo", Arial, sans-serif;
  }
  .card {
    position: absolute;
    left: 320px;
    width: 560px;
    height: 320px;
    border-bottom: 3px solid var(--blue-deep);
    box-shadow: 0 10px 24px rgba(0,0,0,0.25);
  }
  .card--front { top: 50px; background: var(--card); }
  .card--back { top: 420px; background: var(--card-back); }

  .brand {
    position: absolute;
    display: flex;
    align-items: center;
    gap: 18px;
  }
  .brand__dot {
    width: 52px; height: 52px;
    border-radius: 50%;
    background: var(--blue);
    flex: none;
  }
  .brand__name {
    font-family: "Michroma", sans-serif;
    color: var(--blue);
    line-height: 1.15;
    text-transform: uppercase;
  }
  .brand__name span { display: block; }
  .brand__name .brand__line1 { font-size: 30px; letter-spacing: 1px; }
  .brand__name .brand__line2 { font-size: 18px; letter-spacing: 6px; padding-left: 40px; }
  .card--front .brand { left: 130px; top: 48px; }

  .card--back .brand { left: 112px; top: 122px; }
  .card--back .brand__dot { background: var(--emboss); }
  .card--back .brand__name { color: var(--emboss); }

  .person { position: absolute; left: 36px; top: 160px; }
  .person__name {
    font-family: "Michroma", sans-serif;
    font-size: 24px;
    color: var(--blue);
    text-transform: uppercase;
    letter-spacing: 1px;
  }
  .person__title { font-size: 16px; color: var(--white); margin-top: 4px; }

  .divider {
    position: absolute;
    left: 36px; right: 36px; top: 232px;
    height: 1px; background: var(--blue);
  }
  .contact { position: absolute; left: 36px; top: 246px; list-style: none; }
  .contact__item {
    display: flex; align-items: center; gap: 10px;
    font-size: 15px; color: var(--white); line-height: 24px;
  }
  .contact__icon { width: 14px; height: 14px; flex: none; }
</style>
</head>
<body>
  <section class="card card--front" aria-label="Business card front">
    <div class="brand">
      <div class="brand__dot"></div>
      <div class="brand__name"><span class="brand__line1">Halvern</span><span class="brand__line2">Electric</span></div>
    </div>
    <div class="person">
      <p class="person__name">Ned Fosky</p>
      <p class="person__title">Journeyman Electrician</p>
    </div>
    <div class="divider"></div>
    <ul class="contact">
      <li class="contact__item">
        <svg class="contact__icon" viewBox="0 0 24 24" aria-hidden="true"><path fill="#1a8fe3" d="M6.6 10.8a15.1 15.1 0 0 0 6.6 6.6l2.2-2.2a1 1 0 0 1 1-.25 11.4 11.4 0 0 0 3.6.57 1 1 0 0 1 1 1V20a1 1 0 0 1-1 1A17 17 0 0 1 3 4a1 1 0 0 1 1-1h3.5a1 1 0 0 1 1 1c0 1.25.2 2.45.57 3.57a1 1 0 0 1-.25 1z"/></svg>
        1.555.208.3471
      </li>
      <li class="contact__item">
        <svg class="contact__icon" viewBox="0 0 24 24" aria-hidden="true"><path fill="#1a8fe3" d="M2 5h20v14H2z"/><path fill="none" stroke="#1e1e1f" stroke-width="1.6" d="M2 5l10 8 10-8"/></svg>
        KQLHalvernElectric@quellmail.net
      </li>
    </ul>
  </section>

  <section class="card card--back" aria-label="Business card back">
    <div class="brand">
      <div class="brand__dot"></div>
      <div class="brand__name"><span class="brand__line1">Halvern</span><span class="brand__line2">Electric</span></div>
    </div>
  </section>
</body>
</html>
```